We need packaging box design for our solar lights

We need a design for our solar string lights packaging boxes. The final design should communicate an added enjoyment, comfort and beauty when our lights are used to light up warm evening nights in places like backyard, patio restaurant or even family event.

Front and back side of box can be more visual while sides can be used for technical information about the product. There are 2 types of boxes which will have same design - except they need to indicate difference in # of bulbs 10 or 16 . also size of 16 bulb product box is slightly larger so design will need to be slightly adjusted.

Our original logo needs to have "Meadowglow Lamps" text added to it as well.

We put all together in the attachment with some of the examples of photos we like.

Below are more attached files:
1st attachment - general info and samples of photos
Second attachments are photos of our product - they can be adjusted/photoshoped in any way you wish to make the design - or any other acceptable photos you create can be used
Third set of attachments are box templates for 10 and 16 bulbs size box
last are files for logo - choose any you like, edit any colors / text needs to be added/changed to "Meadowglow Lamps " - not Meadowglow Lamps

Target Market(s)

People with yards, patios, restaurants, wedding places... any celebrations or just relaxing during nice warm evening in the beautifully lit place...

Colors

Designer to choose colors to be used in the design.

Requirements
Must have
• indication of bulb numbers
• logo and name Meadowglow lamps
• rest is up to creativity of designer
Nice to have
• some icons

```html
<!DOCTYPE html>
<html lang="en">
<head>
<meta charset="utf-8">
<title>Meadowglow Lamps – Solar String Lights Box Dieline</title>
<link rel="stylesheet" href="https://fonts.googleapis.com/css2?family=Oswald:wght@600;700&family=Roboto+Slab:wght@700&family=Roboto+Condensed:wght@400;700&display=swap">
<style>
  :root {
    --paper: #ffffff;
    --cut-line: #000000;
    --flap-navy: #050a6b;
    --panel-navy: #0b1b57;
    --hex-frame: #1c3cc7;
    --gold: #d9b56a;
    --gold-deep: #6b4a17;
    --icon-green: #1e9b1e;
    --heading-green: #b6f200;
    --body-orange: #f7941d;
    --white: #ffffff;
  }
  html, body {
    margin: 0;
    padding: 0;
    width: 1094px;
    height: 1200px;
    overflow: hidden;
    background: var(--paper);
  }
  .dieline { display: block; width: 1094px; height: 1200px; }
  .cut-frame { fill: none; stroke: var(--cut-line); stroke-width: 1.2; }
  .flap { fill: var(--flap-navy); }
  .panel { fill: var(--panel-navy); }
  .brand-name { font-family: 'Oswald', sans-serif; font-weight: 700; fill: var(--gold); letter-spacing: 0.5px; }
  .brand-sub { font-family: 'Roboto Slab', serif; font-weight: 700; fill: var(--white); }
  .feature-icon { fill: var(--icon-green); stroke: var(--white); stroke-width: 1.2; }
  .icon-glyph { fill: var(--white); }
  .icon-label { font-family: 'Roboto Condensed', sans-serif; font-size: 3.4px; fill: var(--white); text-anchor: middle; }
  .photo-hex { stroke: var(--hex-frame); stroke-width: 3; }
  .bulb-badge { fill: url(#badgeGold); stroke: var(--white); stroke-width: 1.5; }
  .badge-number { font-family: 'Oswald', sans-serif; font-weight: 700; font-size: 22px; fill: var(--white); text-anchor: middle; }
  .badge-word { font-family: 'Oswald', sans-serif; font-weight: 700; font-size: 8px; fill: var(--white); text-anchor: middle; }
  .badge-small { font-family: 'Oswald', sans-serif; font-weight: 600; font-size: 4.6px; fill: var(--white); text-anchor: middle; }
  .maker-name { font-family: 'Roboto Condensed', sans-serif; font-weight: 700; font-size: 5px; fill: var(--white); text-anchor: middle; letter-spacing: 0.6px; }
  .info-heading { font-family: 'Roboto Condensed', sans-serif; font-weight: 700; font-size: 7px; fill: var(--heading-green); }
  .info-body { font-family: 'Roboto Condensed', sans-serif; font-weight: 700; font-size: 6.3px; fill: var(--body-orange); }
</style>
</head>
<body>
<svg class="dieline" viewBox="0 0 848 930" xmlns="http://www.w3.org/2000/svg">
  <defs>
    <linearGradient id="bokehBand" x1="0" y1="0" x2="0" y2="1">
      <stop offset="0" stop-color="#0b1b57"/>
      <stop offset="1" stop-color="#5a4a2a"/>
    </linearGradient>
    <linearGradient id="warmPhoto" x1="0" y1="0" x2="1" y2="1">
      <stop offset="0" stop-color="#3a2a14"/>
      <stop offset="0.5" stop-color="#a87a32"/>
      <stop offset="1" stop-color="#1e160c"/>
    </linearGradient>
    <linearGradient id="badgeGold" x1="0" y1="0" x2="0" y2="1">
      <stop offset="0" stop-color="#c89a4a"/>
      <stop offset="1" stop-color="#4a3010"/>
    </linearGradient>
    <linearGradient id="waveGlow" x1="0" y1="0" x2="1" y2="0">
      <stop offset="0" stop-color="#e8c9a8"/>
      <stop offset="1" stop-color="#3a4a9a"/>
    </linearGradient>
  </defs>

  <rect class="cut-frame" x="1" y="1" width="846" height="927"/>

  <!-- Flaps -->
  <path class="flap" d="M472 340 L512 165 Q516 150 535 148 L811 148 L811 328 L818 340 Z"/>
  <path class="flap" d="M30 560 L472 560 L472 590 L363 730 L363 781 L147 781 L147 730 Z"/>
  <path class="flap" d="M472 560 L818 560 L818 590 L643 730 L643 781 L472 781 Z"/>

  <!-- Front panel -->
  <g class="front-panel">
    <rect class="panel" x="30" y="340" width="442" height="220"/>
    <rect x="30" y="508" width="442" height="52" fill="url(#bokehBand)" role="img" aria-label="Scattered golden glowing bulb bokeh"/>

    <text class="brand-name" x="155" y="405" font-size="33" text-anchor="middle">MEADOWGLOW</text>
    <text class="brand-sub" x="157" y="436" font-size="28" text-anchor="middle">Lamps</text>
    <rect x="112" y="443" width="92" height="1.2" fill="var(--white)" opacity="0.7"/>

    <g class="feature-icons">
      <circle class="feature-icon" cx="106" cy="481" r="18"/>
      <circle class="icon-glyph" cx="106" cy="475" r="4.5"/>
      <g stroke="var(--white)" stroke-width="1.2">
        <line x1="106" y1="466" x2="106" y2="468"/><line x1="106" y1="482" x2="106" y2="484"/>
        <line x1="97" y1="475" x2="99" y2="475"/><line x1="113" y1="475" x2="115" y2="475"/>
      </g>
      <text class="icon-label" x="106" y="489">Charges during</text>
      <text class="icon-label" x="106" y="493">the day</text>

      <circle class="feature-icon" cx="150" cy="481" r="18"/>
      <path class="icon-glyph" d="M152 467 A8 8 0 1 0 158 480 A6 6 0 1 1 152 467 Z"/>
      <text class="icon-label" x="150" y="490">Work at Night</text>

      <circle class="feature-icon" cx="194" cy="481" r="18"/>
      <path class="icon-glyph" d="M194 484 Q186 478 190 468 Q200 472 194 484 Z"/>
      <path class="icon-glyph" d="M195 484 Q198 475 204 474 Q204 482 195 484 Z"/>
      <text class="icon-label" x="194" y="490">Green Energy</text>
    </g>

    <polygon class="photo-hex" points="346,355 390,380 390,430 346,455 302,430 302,380" fill="url(#warmPhoto)" role="img" aria-label="Photo of solar string lights glowing along a patio at night"/>
    <polygon class="photo-hex" points="298,437 342,462 342,512 298,537 254,512 254,462" fill="url(#warmPhoto)" role="img" aria-label="Photo of a single warm bulb glowing in a garden"/>
    <polygon class="photo-hex" points="395,440 439,465 439,515 395,540 351,515 351,465" fill="url(#warmPhoto)" role="img" aria-label="Photo of string lights hanging over a backyard"/>

    <rect class="bulb-badge" x="319" y="479" width="56" height="68" rx="12"/>
    <text class="badge-number" x="347" y="507">10</text>
    <text class="badge-word" x="347" y="519">BULBS</text>
    <text class="badge-small" x="347" y="528">SOLAR STRING</text>
    <text class="badge-small" x="347" y="535">LIGHTS</text>

    <circle cx="428" cy="372" r="4" fill="var(--gold)"/>
    <text class="maker-name" x="428" y="390">MEADOWGLOW</text>
    <text class="maker-name" x="428" y="397">LAMPS</text>
  </g>

  <!-- Back panel -->
  <g class="back-panel">
    <rect class="panel" x="472" y="340" width="346" height="220"/>
    <path d="M476 545 Q560 520 650 540 Q740 560 818 535 L818 560 L476 560 Z" fill="url(#waveGlow)" opacity="0.75"/>
    <path d="M476 552 Q570 530 660 548 Q745 565 818 545" fill="none" stroke="var(--white)" stroke-width="0.8" opacity="0.6"/>

    <text class="info-heading" x="514" y="368">How the Solar Light work:</text>
    <text class="info-body" x="514" y="379">The solar light has a solar panel that converts sunlight into electricity which is stored</text>
    <text class="info-body" x="514" y="390">during the day in the rechargeable batteries. At night, the solar light uses stored</text>
    <text class="info-body" x="514" y="401">energy to light up. The operating time depends on the geographical location, season</text>
    <text class="info-body" x="514" y="412">and daily weather condition.</text>

    <text class="info-heading" x="514" y="434">Where to place solar panel:</text>
    <text class="info-body" x="514" y="445">For maximum effectiveness place the solar panel in the location with full, direct</text>
    <text class="info-body" x="514" y="456">sunlight.</text>

    <text class="info-heading" x="514" y="478">How To Install Solar Pane</text>
    <text class="info-body" x="514" y="489">Earth Spike: simply insert the ground stake (included ) into the ground until it is</text>
    <text class="info-body" x="514" y="500">firmly in place.</text>
    <text class="info-body" x="514" y="511">Wall Mount: simply mount the solar panel onto the wall with two screws (included )</text>
    <text class="info-body" x="514" y="522">and adjust the angle of solar panel for maximum sun exposure.</text>
  </g>
</svg>
</body>
</html>
```